Modern looking signage for dental office.

Exterior signage for passing cars
Updates
Need extra days to review
Target Market(s)
Cars passing by
Font styles to use
Sans Serif
Colors
3276b5
Requirements
Must have
- Logo
- OPEN ON SUTURDAY AND SUNDAY
- NIGHT CLINIC AVAILABLE
- PLEASE USE THE FONT TYPE IN FILE 4 UPLOADED BELOW.
- (847) 302-7469
- Modern looking

```html
<!DOCTYPE html>
<html lang="en">
<head>
<meta charset="utf-8">
<title>Peak Dental – Weekend &amp; Night Clinic Sign</title>
<link rel="stylesheet" href="https://fonts.googleapis.com/css2?family=Montserrat:wght@300;400;500;800;900&display=swap">
<style>
  :root {
    --page-bg: #9a9a9a;
    --sign-white: #ffffff;
    --sign-grey-top: #c9c9c9;
    --sign-grey-bottom: #bdbdbd;
    --band-grey: #e2e2e2;
    --ink: #0d0d0d;
    --brand-ink: #3c3c3c;
    --tagline-ink: #4a4a4a;
  }
  * { box-sizing: border-box; margin: 0; padding: 0; }
  html, body {
    width: 1200px; height: 1000px; overflow: hidden;
    background: var(--page-bg);
    font-family: "Montserrat", sans-serif;
  }
  .sign {
    position: absolute; left: 195px; top: 95px;
    width: 810px; height: 810px;
    background: linear-gradient(180deg, var(--sign-grey-top), var(--sign-grey-bottom));
    overflow: hidden;
  }
  .sign__shapes { position: absolute; inset: 0; }
  .brand {
    position: absolute; left: 65px; top: 55px;
    display: flex; align-items: center; gap: 22px;
  }
  .brand__circle {
    flex: none;
    width: 148px; height: 148px; border-radius: 50%;
    border: 3px solid var(--brand-ink);
  }
  .brand__name {
    font-weight: 300; font-size: 62px; letter-spacing: 0;
    color: var(--brand-ink); line-height: 1; white-space: nowrap;
    padding-bottom: 8px;
  }
  .brand__tagline {
    position: absolute; left: 275px; width: 410px; top: 183px;
    text-align: center; white-space: nowrap;
    font-weight: 500; font-size: 23px; letter-spacing: 0.3px;
    color: var(--tagline-ink);
  }
  .message {
    position: absolute; left: 0; right: 0; text-align: center;
    color: var(--ink); line-height: 1; white-space: nowrap;
  }
  .message--open { top: 365px; font-weight: 900; font-size: 92px; }
  .message--days { top: 453px; font-weight: 900; font-size: 54px; }
  .message--night { top: 550px; font-weight: 500; font-size: 50px; }
  .message--hours { top: 604px; font-weight: 900; font-size: 51px; }
  .divider {
    position: absolute; left: 210px; top: 521px;
    width: 390px; height: 3px; background: var(--ink);
  }
  .contact-band {
    position: absolute; left: 0; right: 0; top: 671px; bottom: 0;
    background: var(--band-grey);
    border-top: 6px solid var(--ink);
    display: flex; align-items: center; justify-content: center; gap: 22px;
    padding-bottom: 4px;
  }
  .contact-band__icon { width: 64px; height: 64px; flex: none; }
  .contact-band__phone {
    font-weight: 900; font-size: 75px; color: var(--ink); letter-spacing: 1px;
    white-space: nowrap;
  }
</style>
</head>
<body>
  <main class="sign">
    <svg class="sign__shapes" width="810" height="810" viewBox="0 0 810 810" aria-hidden="true">
      <defs>
        <linearGradient id="header-fade" x1="0" y1="0" x2="0" y2="1">
          <stop offset="0" stop-color="#ffffff"/>
          <stop offset="1" stop-color="#f2f2f2"/>
        </linearGradient>
      </defs>
      <polygon points="0,0 810,0 810,240 402,318 0,240" fill="url(#header-fade)"/>
      <polygon points="255,300 550,300 402,345" fill="#111111"/>
    </svg>

    <div class="brand">
      <span class="brand__circle"></span>
      <span class="brand__name">PEAK DENTAL</span>
    </div>
    <p class="brand__tagline">MODERN GENERAL DENTISTRY</p>

    <p class="message message--open">OPEN ON</p>
    <p class="message message--days">SATURDAY AND SUNDAY</p>
    <span class="divider"></span>
    <p class="message message--night">NIGHT CLINIC FROM</p>
    <p class="message message--hours">5PM TO 10PM AVAILABLE</p>

    <div class="contact-band">
      <svg class="contact-band__icon" viewBox="0 0 64 64" aria-hidden="true">
        <circle cx="32" cy="32" r="29" fill="#ffffff" stroke="#333" stroke-width="3"/>
        <path d="M22 18c2-2 4-2 5 0l3 6c1 2 0 3-1 4l-2 2c1 4 4 7 8 9l2-2c1-1 2-2 4-1l6 3c2 1 2 3 0 5l-3 3c-3 2-8 1-14-4s-11-12-11-17c0-3 1-5 3-8z" fill="#111"/>
        <path d="M36 20a9 9 0 0 1 8 8M36 14a15 15 0 0 1 14 14" fill="none" stroke="#111" stroke-width="2.5" stroke-linecap="round"/>
      </svg>
      <span class="contact-band__phone">847 302 7469</span>
    </div>
  </main>
</body>
</html>
```